Velmora Cabinets Letter Head and Email Signature

Hi
I would love a design package for a letterhead, email signature, even update my business card if you like if you can come up with a great idea for my new high end cabinet shop. Velmora Cabinets brings timeless craftsmanship to modern interiors, specializing in high end, custom cabinetry designed for architects and interior designers.

Target Market(s)

high end, luxury market

Industry/Entity Type

cabinet making

Requirements
Must have
• my colours of logo as the theme

```html
<!DOCTYPE html>
<html lang="en">
<head>
<meta charset="utf-8">
<title>Velmora Cabinets – Email Signature</title>
<link href="https://fonts.googleapis.com/css2?family=Michroma&family=Montserrat:wght@400;500;800&display=swap" rel="stylesheet">
<style>
  :root {
    --page: #ffffff;
    --ink-black: #000000;
    --brand-green: #4c8a48;
    --brand-green-deep: #2f5a2d;
    --text-white: #ffffff;
    --caption-grey: #a3a3a3;
    --shadow: rgba(0, 0, 0, 0.35);
  }
  * { margin: 0; padding: 0; box-sizing: border-box; }
  html, body {
    width: 1200px; height: 723px; overflow: hidden;
    background: var(--page);
  }
  .board { position: relative; width: 1200px; height: 723px; }

  .signature {
    position: absolute; left: 64px; top: 104px;
    width: 1073px; height: 357px;
    background:
      radial-gradient(ellipse 260px 240px at 0% 100%, var(--brand-green-deep) 0%, rgba(47,90,45,0.35) 45%, rgba(0,0,0,0) 100%),
      var(--ink-black);
    box-shadow: 14px 26px 22px var(--shadow);
    overflow: hidden;
  }
  .signature__pattern {
    position: absolute; inset: 0;
    background: linear-gradient(90deg, rgba(0,0,0,0) 0%, rgba(255,255,255,0.03) 50%, rgba(255,255,255,0.05) 100%);
  }

  .brand {
    position: absolute; left: 48px; top: 142px;
    display: flex; align-items: center; gap: 18px;
  }
  .brand__mark {
    width: 26px; height: 26px; background: var(--brand-green);
  }
  .brand__name {
    font-family: "Montserrat", sans-serif; font-weight: 500;
    color: var(--brand-green); line-height: 1;
  }
  .brand__name-main { display: block; font-size: 50px; letter-spacing: 1px; }
  .brand__name-sub { display: block; font-size: 25px; letter-spacing: 9px; margin-top: 6px; text-transform: uppercase; }

  .contact-card { position: absolute; left: 458px; top: 72px; }
  .person__name {
    font-family: "Michroma", sans-serif; font-size: 21px; font-weight: 400;
    color: var(--text-white); letter-spacing: 0.5px; line-height: 1;
    -webkit-text-stroke: 0.6px currentColor;
  }
  .person__surname { color: var(--brand-green); }
  .person__role {
    margin-top: 12px;
    font-family: "Montserrat", sans-serif; font-size: 16px; font-weight: 500;
    color: var(--text-white); letter-spacing: 2.4px;
  }
  .divider {
    width: 58px; height: 2px; background: var(--text-white);
    margin: 20px 0 0 2px;
  }
  .contact-list { list-style: none; margin-top: 24px; margin-left: -6px; }
  .contact-list__item {
    display: flex; align-items: center; gap: 14px; height: 38px;
    font-family: "Montserrat", sans-serif; font-size: 22px; font-weight: 400;
    color: var(--text-white);
  }
  .contact-icon { width: 42px; height: 36px; flex: none; }
</style>
</head>
<body>
<main class="board">
  <section class="signature" aria-label="Email signature">
    <div class="signature__pattern" role="img" aria-label="Faint repeating brand pattern on black"></div>

    <div class="brand">
      <span class="brand__mark" aria-hidden="true"></span>
      <p class="brand__name">
        <span class="brand__name-main">Velmora</span>
        <span class="brand__name-sub">Cabinets</span>
      </p>
    </div>

    <div class="contact-card">
      <h1 class="person__name">ROWAN <span class="person__surname">TESSLER</span></h1>
      <p class="person__role">Director Craftsman</p>
      <div class="divider"></div>
      <ul class="contact-list">
        <li class="contact-list__item">
          <svg class="contact-icon" viewBox="0 0 42 36" aria-hidden="true">
            <polygon points="11,2 31,2 40,18 31,34 11,34 2,18" fill="none" stroke="#4c8a48" stroke-width="1.6"/>
            <circle cx="21" cy="18" r="9" fill="#4c8a48"/>
            <path d="M17.5 13.5c-.8.8-.6 3 1.6 5.4s4.4 2.6 5.3 1.7l.9-.9-2-1.9-1 .8c-.8-.3-2.1-1.6-2.4-2.4l.8-1-1.9-2z" fill="#000"/>
          </svg>
          <span>0400555182</span>
        </li>
        <li class="contact-list__item">
          <svg class="contact-icon" viewBox="0 0 42 36" aria-hidden="true">
            <polygon points="11,2 31,2 40,18 31,34 11,34 2,18" fill="none" stroke="#4c8a48" stroke-width="1.6"/>
            <circle cx="21" cy="18" r="9" fill="#4c8a48"/>
            <rect x="15.5" y="14" width="11" height="8" fill="#000"/>
            <path d="M15.5 14l5.5 4.5 5.5-4.5" fill="none" stroke="#4c8a48" stroke-width="1"/>
          </svg>
          <span>info@velmoracabinets.com.au</span>
        </li>
        <li class="contact-list__item">
          <svg class="contact-icon" viewBox="0 0 42 36" aria-hidden="true">
            <polygon points="11,2 31,2 40,18 31,34 11,34 2,18" fill="none" stroke="#4c8a48" stroke-width="1.6"/>
            <circle cx="21" cy="18" r="9" fill="#4c8a48"/>
          </svg>
          <span>@velmora.cabinets</span>
        </li>
      </ul>
    </div>
  </section>
</main>
</body>
</html>
```